RWT Fittings Ltd Business Cards

We need a business card with our business logo. We provide window and door installations on high-rises in west coast British Colombia, Canada.

I would like my business information and details on one side of the card, and the other side the company name with logo

Target Market(s)

General Contractors

Industry/Entity Type

Construction

Contact Information for Business Card

one side i want my company name and logo in the dark theme logo that i provided

Requirements
Must have
• Marco Peltieri, 16045518293, RWTFittings@mailbox-demo.com, 1407-5194 Linden Row Burnaby BC, V5H 2K9, Owner & Manager

```html
<!DOCTYPE html>
<html lang="en">
<head>
<meta charset="utf-8">
<title>RWT Fittings Ltd – Business Cards</title>
<link rel="stylesheet" href="https://fonts.googleapis.com/css2?family=Open+Sans:wght@400;600;700&display=swap">
<style>
  :root {
    --backdrop: #232325;
    --card: #1f1f24;
    --accent: #29a8e0;
    --text: #ffffff;
    --steel: #9a9a9c;
    --rule: #8c8c90;
    --emboss: #3b3b43;
  }
  * { box-sizing: border-box; margin: 0; padding: 0; }
  html, body { width: 1200px; height: 780px; overflow: hidden; }
  body {
    background: var(--backdrop);
    font-family: "Open Sans", Arial, sans-serif;
    position: relative;
  }
  .card {
    position: absolute;
    top: 235px;
    width: 540px;
    height: 309px;
    background: var(--card);
    overflow: hidden;
  }
  .card--info { left: 40px; }
  .card--brand { left: 620px; }

  /* brand lockup */
  .brand {
    position: absolute;
    display: flex;
    align-items: center;
    gap: 10px;
    font-weight: 700;
    white-space: nowrap;
  }
  .brand__mark { display: block; flex: none; }
  .card--info .brand { left: 28px; top: 88px; color: var(--accent); font-size: 22px; }
  .card--info .brand__mark { width: 20px; height: 20px; background: var(--accent); }
  .card--brand .brand {
    left: 50%; top: 50%;
    transform: translate(-50%, -50%);
    color: var(--emboss);
    font-size: 40px;
    gap: 18px;
  }
  .card--brand .brand__mark { width: 36px; height: 36px; background: var(--emboss); }

  .divider { position: absolute; left: 0; top: 0; }

  .holder { position: absolute; left: 296px; top: 62px; }
  .holder__name { color: var(--accent); font-weight: 700; font-size: 30px; line-height: 1.1; }
  .holder__title { color: var(--text); font-size: 15px; font-weight: 400; margin-top: 2px; }

  .contacts { position: absolute; left: 296px; top: 140px; list-style: none; }
  .contacts li {
    display: flex; align-items: center; gap: 9px;
    color: var(--text); font-size: 14px; line-height: 26px;
    white-space: nowrap;
  }
  .contacts svg { width: 14px; height: 14px; flex: none; }

  .address-band {
    position: absolute; left: 0; top: 248px;
    width: 420px; height: 34px;
    background: var(--accent);
    color: var(--text);
    font-size: 13.5px;
    line-height: 34px;
    padding-left: 22px;
    white-space: nowrap;
  }
  .corner-mark {
    position: absolute; left: 436px; top: 252px;
    width: 26px; height: 26px; background: var(--accent);
  }
  .corner-block {
    position: absolute; right: 0; bottom: 0;
    width: 62px; height: 44px; background: var(--steel);
  }
</style>
</head>
<body>
  <section class="card card--info" aria-label="Business card, contact side">
    <div class="brand"><span class="brand__mark"></span>RWT Fittings Ltd</div>

    <svg class="divider" width="540" height="309" aria-hidden="true">
      <line x1="312" y1="40" x2="212" y2="232" stroke="var(--rule)" stroke-width="1"/>
    </svg>

    <div class="holder">
      <h1 class="holder__name">Marco Peltieri</h1>
      <p class="holder__title">Owner &amp; Manager</p>
    </div>

    <ul class="contacts">
      <li>
        <svg viewBox="0 0 24 24" aria-hidden="true"><path fill="var(--accent)" d="M6.6 10.8a15 15 0 0 0 6.6 6.6l2.2-2.2c.3-.3.7-.4 1-.2 1.1.4 2.3.6 3.6.6.6 0 1 .4 1 1V20c0 .6-.4 1-1 1A17 17 0 0 1 3 4c0-.6.4-1 1-1h3.5c.6 0 1 .4 1 1 0 1.3.2 2.5.6 3.6.1.3 0 .7-.2 1z"/></svg>
        (604) 551-8293
      </li>
      <li>
        <svg viewBox="0 0 24 24" aria-hidden="true"><rect x="2" y="5" width="20" height="14" rx="2" fill="var(--accent)"/><path d="M3 6l9 7 9-7" fill="none" stroke="var(--card)" stroke-width="1.8"/></svg>
        RWTFittings@mailbox-demo.com
      </li>
      <li>
        <svg viewBox="0 0 24 24" aria-hidden="true"><circle cx="12" cy="12" r="10" fill="var(--accent)"/><path d="M2 12h20M12 2c3 3 3 17 0 20M12 2c-3 3-3 17 0 20" fill="none" stroke="var(--card)" stroke-width="1.4"/></svg>
        www.rwtfittings-demo.com
      </li>
    </ul>

    <div class="address-band">1407-5194 Linden Row Burnaby BC, V5H 2K9</div>
    <span class="corner-mark" aria-hidden="true"></span>
    <span class="corner-block" aria-hidden="true"></span>
  </section>

  <section class="card card--brand" aria-label="Business card, company side">
    <div class="brand"><span class="brand__mark"></span>RWT Fittings Ltd</div>
  </section>
</body>
</html>
```